Website for Dental Office - The Bright Arch Clinic

The bright arch clinic is a dental office offering cosmetic dentistry, general dentistry, and multi-specialty dental care all under one roof in our state-of-the-art cosmetic dental center. We are particularly striving to provide services that fit the need of the young generation. Thus, we hope to have a modern, professional concise website that represents our spirit.

*Should be able to switch from English to Chinese

6 sections besides homepage:
Home, Meet us, Services,
Patient Info, Cases&Reviews, Blog, Contact

The Services sections should contain multiple subsections such as cleaning and prevention, cosmetic dentistry, implant dentistry, removable dentures, etc...
The Patient Info section is also intended to contain several subsections such as
New Patient offer, accepted Insurance, patient portal, helpful tips, etc...

Target Market(s)

young generation

Coding

Coded - Design and coding required

Number of Pages Required

5+ page

Font styles to use
Sans Serif

Colors
0592cd
33a6d7
85cae6
00a990
33b8a4
86cfc6
cee9f5
cfeae6
3277b5

Requirements
Must have
• *Should be able to switch from English to Chinese
Nice to have
• http://www.thebrightarchclinic.com/
• As a reference, the above link is the current website, but we would like to change the appearance and the content (our new logo's picture is attached)

```html
<!DOCTYPE html>
<html lang="en">
<head>
<meta charset="utf-8">
<title>Services – The Bright Arch Clinic</title>
<link href="https://fonts.googleapis.com/css2?family=Montserrat:wght@500;600;700;800&family=Nunito+Sans:wght@400;600;700&display=swap" rel="stylesheet">
<style>
:root{
  --blue:#0592cd; --blue-mid:#33a6d7; --blue-light:#85cae6; --blue-pale:#cee9f5;
  --green:#00a990; --green-mid:#33b8a4; --green-light:#86cfc6;
  --navy:#3277b5; --ink:#111; --text:#555; --muted:#777;
  --grey-bg:#f1f1f1; --grey-bar:#e8e8e8;
}
*{margin:0;padding:0;box-sizing:border-box}
html,body{width:1084px;height:1200px;overflow:hidden}
body{position:relative;background:#fff;font-family:"Nunito Sans",sans-serif;color:var(--text)}
.abs{position:absolute}
.hero-bg{left:0;top:0;width:1084px;height:560px;background:linear-gradient(180deg,#d9f0fb 0%,#e4f4fb 55%,#fff 100%)}
.top-curve{left:0;top:0}
.top-line{left:0;top:0;width:1084px;height:2px;background:var(--navy)}
.brand{left:146px;top:17px;display:flex;align-items:center;gap:10px}
.brand-mark{width:40px;height:40px;background:var(--blue-mid);border-radius:4px}
.brand-name{font-family:"Montserrat",sans-serif;font-weight:700;font-size:14px;line-height:1.1;color:var(--blue-mid);width:150px}
.nav{top:36px;font-family:"Montserrat",sans-serif;font-weight:500;font-size:9.5px;color:#555;letter-spacing:.1px}
.nav.active{color:var(--green)}
.phone-bubble{left:781px;top:-14px;width:102px;height:102px;border-radius:50%;background:var(--navy);color:#fff;text-align:center}
.phone-bubble svg{position:absolute;left:40px;top:28px}
.phone-bubble span{position:absolute;left:0;right:0;top:57px;font-family:"Montserrat",sans-serif;font-weight:700;font-size:11px}
.lang{left:893px;top:26px;width:45px;height:27px;border-radius:3px;background:var(--green);color:#fff;font-size:9px;display:flex;align-items:center;justify-content:center;gap:4px}
.title{left:0;width:1084px;top:193px;text-align:center;font-family:"Montserrat",sans-serif;font-weight:800;font-size:38px;color:var(--ink);letter-spacing:.5px}
.intro{left:310px;width:464px;top:252px;text-align:center;font-size:10px;line-height:17.5px;color:#555}
.card{width:176px;height:176px;background:#fff;border-radius:3px;box-shadow:0 0 10px rgba(133,202,230,.35)}
.card-icon{position:absolute;left:14px;top:44px;width:47px;height:34px;border-radius:6px}
.card h3{position:absolute;left:15px;right:8px;top:92px;font-family:"Montserrat",sans-serif;font-weight:700;font-size:11px;line-height:20px;color:var(--ink)}
.card p{position:absolute;left:16px;width:142px;top:113px;font-size:9.5px;line-height:16px;color:#666}
.card.tall h3{top:78px}
.card.tall p{top:123px}
.grey-band{left:0;top:869px;width:1084px;height:291px;background:var(--grey-bg)}
.cta{left:146px;top:795px}
.cta-small{left:165px;top:845px;font-size:10.5px;color:#fff}
.cta-head{left:165px;top:862px;font-family:"Montserrat",sans-serif;font-weight:700;font-size:32px;color:#fff}
.cta-btn{left:707px;top:867px;width:203px;height:41px;border-radius:21px;background:#fff;color:#222;font-family:"Montserrat",sans-serif;font-weight:700;font-size:11px;display:flex;align-items:center;justify-content:center;letter-spacing:.3px}
.foot-brand{left:146px;top:990px;width:176px;text-align:center}
.foot-mark{width:90px;height:60px;margin:0 auto 10px;background:var(--blue-light);border-radius:6px}
.foot-name{font-family:"Montserrat",sans-serif;font-weight:700;font-size:13px;color:var(--blue-mid)}
.social{top:1090px;width:30px;height:30px;border-radius:50%}
.foot-head{top:983px;font-family:"Montserrat",sans-serif;font-weight:700;font-size:10.5px;color:#333;letter-spacing:.3px}
.foot-list{top:1008px;list-style:none;font-size:9.5px;line-height:17px;color:#666}
.hours{top:1008px;font-size:9.5px;line-height:17px;color:#666;border-collapse:collapse}
.hours td{padding:0}
.hours td.day{width:90px}
.hours td.time{font-family:"Montserrat",sans-serif;font-weight:700;font-size:9px;color:#444}
.contact-row{left:770px;display:flex;gap:8px;font-size:9.5px;line-height:17px;color:#666}
.contact-row.big{font-size:13px;color:#555;font-weight:600}
.bottom-bar{left:0;top:1160px;width:1084px;height:40px;background:var(--grey-bar)}
.copy{left:147px;top:1172px;font-size:9.5px;color:#888}
.copy a,.credit{color:var(--navy);text-decoration:none}
.credit{left:760px;top:1172px;width:177px;text-align:right;font-size:9.5px;color:var(--green)}
</style>
</head>
<body>
<div class="abs hero-bg"></div>
<svg class="abs top-curve" width="1084" height="140" viewBox="0 0 1084 140" aria-hidden="true">
  <path d="M0 0H1084V61Q542 200 0 61Z" fill="#fff"/>
</svg>
<div class="abs top-line"></div>

<header>
  <div class="abs brand"><div class="brand-mark"></div><div class="brand-name">THE BRIGHT ARCH<br>CLINIC</div></div>
  <nav>
    <span class="abs nav" style="left:359px">HOME</span>
    <span class="abs nav" style="left:406px">MEET US</span>
    <span class="abs nav active" style="left:465px">SERVICES</span>
    <span class="abs nav" style="left:529px">PATIENT INFO</span>
    <span class="abs nav" style="left:615px">REVIEWS</span>
    <span class="abs nav" style="left:675px">BLOG</span>
    <span class="abs nav" style="left:721px">CONTACT</span>
  </nav>
  <div class="abs phone-bubble">
    <svg width="22" height="22" viewBox="0 0 24 24" aria-hidden="true"><path fill="#fff" d="M6.6 10.8a15.1 15.1 0 0 0 6.6 6.6l2.2-2.2a1 1 0 0 1 1-.25 11.4 11.4 0 0 0 3.6.57 1 1 0 0 1 1 1V20a1 1 0 0 1-1 1A17 17 0 0 1 3 4a1 1 0 0 1 1-1h3.5a1 1 0 0 1 1 1c0 1.25.2 2.45.57 3.57a1 1 0 0 1-.25 1z"/></svg>
    <span>555.210.4870</span>
  </div>
  <div class="abs lang">汉语
    <svg width="8" height="6" viewBox="0 0 8 6" aria-hidden="true"><path d="M1 1l3 3 3-3" stroke="#fff" stroke-width="1.5" fill="none"/></svg>
  </div>
</header>

<main>
  <h1 class="abs title">SERVICES</h1>
  <p class="abs intro">Lorem Ipsum is dummy text of the printing and typesetting industry. Lorem Ipsum has been the industry's standard dummy text.</p>

  <article class="abs card" style="left:146px;top:325px"><div class="card-icon" role="img" aria-label="Cleaning icon" style="background:var(--blue-pale)"></div><h3>Cleaning and Prevention</h3><p>Lorem Ipsum is dummy text of the printing and typesetting.</p></article>
  <article class="abs card" style="left:350px;top:325px"><div class="card-icon" role="img" aria-label="Cosmetic dentistry icon" style="background:var(--blue-pale)"></div><h3>Cosmetic Dentistry</h3><p>Lorem Ipsum is dummy text of the printing and typesetting.</p></article>
  <article class="abs card" style="left:556px;top:325px"><div class="card-icon" role="img" aria-label="Orthodontics icon" style="background:var(--green-light)"></div><h3>Orthodontics</h3><p>Lorem Ipsum is dummy text of the printing and typesetting.</p></article>
  <article class="abs card" style="left:761px;top:325px"><div class="card-icon" role="img" aria-label="Dentures icon" style="background:var(--blue-pale)"></div><h3>Removable Dentures</h3><p>Lorem Ipsum is dummy text of the printing and typesetting.</p></article>

  <article class="abs card" style="left:146px;top:535px"><div class="card-icon" role="img" aria-label="Implant icon" style="background:var(--blue-pale)"></div><h3>Implant Dentistry</h3><p>Lorem Ipsum is dummy text of the printing and typesetting.</p></article>
  <article class="abs card" style="left:350px;top:535px"><div class="card-icon" role="img" aria-label="Aligner icon" style="background:var(--blue-pale)"></div><h3>Clear Aligners</h3><p>Lorem Ipsum is dummy text of the printing and typesetting.</p></article>
  <article class="abs card" style="left:556px;top:535px"><div class="card-icon" role="img" aria-label="Pediatric dentistry icon" style="background:var(--green-light)"></div><h3>Pediatric Dentistry</h3><p>Lorem Ipsum is dummy text of the printing and typesetting.</p></article>
  <article class="abs card tall" style="left:761px;top:535px"><div class="card-icon" role="img" aria-label="Multi-specialty icon" style="top:30px;background:var(--blue-pale)"></div><h3>Multi-specialty<br>Treatment</h3><p>Lorem Ipsum is dummy text of the printing and typesetting.</p></article>

  <div class="abs grey-band"></div>
  <svg class="abs cta" width="793" height="151" viewBox="0 0 793 151" aria-hidden="true">
    <defs><linearGradient id="ctaGrad" x1="0" y1="0" x2="1" y2="0"><stop offset="0" stop-color="#0592cd"/><stop offset="1" stop-color="#00a990"/></linearGradient></defs>
    <path d="M5 0L787 41Q793 41 793 47V145Q793 151 787 151H6Q0 151 0 145V5Q0 0 5 0Z" fill="url(#ctaGrad)"/>
  </svg>
  <p class="abs cta-small">Lorem Ipsum is dummy text of the printing and typesetting.</p>
  <h2 class="abs cta-head">YOUR SMILE. OUR PASSION.</h2>
  <a class="abs cta-btn">BOOK AN APPOINTMENT</a>
</main>

<footer>
  <div class="abs foot-brand"><div class="foot-mark"></div><div class="foot-name">THE BRIGHT ARCH CLINIC</div></div>
  <span class="abs social" style="left:163px;background:var(--blue-mid)"></span>
  <span class="abs social" style="left:201px;background:var(--navy)"></span>
  <span class="abs social" style="left:238px;background:var(--green)"></span>
  <span class="abs social" style="left:276px;background:var(--green-mid)"></span>

  <h4 class="abs foot-head" style="left:353px">USEFUL LINKS</h4>
  <ul class="abs foot-list" style="left:352px">
    <li>Home</li><li>Meet Us</li><li>Services</li><li>Patient Info</li><li>Case &amp; Reviews</li><li>Blog</li><li>Contact</li>
  </ul>

  <h4 class="abs foot-head" style="left:558px">OPENING HOURS</h4>
  <table class="abs hours" style="left:558px">
    <tr><td class="day">Sunday &amp; Monday</td><td class="time">Closed</td></tr>
    <tr><td class="day">Tuesday</td><td class="time">9:30AM – 5:00PM</td></tr>
    <tr><td class="day">Wednesday</td><td class="time">Closed</td></tr>
    <tr><td class="day">Thursday</td><td class="time">9:30AM – 5:00PM</td></tr>
    <tr><td class="day">Friday</td><td class="time">9:00AM – 5:00PM</td></tr>
    <tr><td class="day">Saturday</td><td class="time">9:00AM – 5:00PM</td></tr>
  </table>

  <h4 class="abs foot-head" style="left:764px">CONTACT INFO</h4>
  <div class="abs contact-row" style="top:1008px">
    <svg width="10" height="14" viewBox="0 0 10 14" style="margin-top:3px" aria-hidden="true"><path d="M5 0a5 5 0 0 0-5 5c0 3.8 5 9 5 9s5-5.2 5-9a5 5 0 0 0-5-5zm0 7a2 2 0 1 1 0-4 2 2 0 0 1 0 4z" fill="var(--green)"/></svg>
    <span>27 Maple Row, Suite 12,<br>Harbor Falls MA 01234</span>
  </div>
  <div class="abs contact-row big" style="top:1051px;left:763px">
    <svg width="13" height="13" viewBox="0 0 24 24" style="margin-top:3px" aria-hidden="true"><path fill="var(--navy)" d="M6.6 10.8a15.1 15.1 0 0 0 6.6 6.6l2.2-2.2a1 1 0 0 1 1-.25 11.4 11.4 0 0 0 3.6.57 1 1 0 0 1 1 1V20a1 1 0 0 1-1 1A17 17 0 0 1 3 4a1 1 0 0 1 1-1h3.5a1 1 0 0 1 1 1c0 1.25.2 2.45.57 3.57a1 1 0 0 1-.25 1z"/></svg>
    <span>555.210.4870</span>
  </div>
  <div class="abs contact-row" style="top:1083px;left:763px">
    <svg width="14" height="10" viewBox="0 0 14 10" style="margin-top:4px" aria-hidden="true"><rect width="14" height="10" rx="1" fill="var(--blue-mid)"/><path d="M0.5 1L7 6l6.5-5" stroke="#fff" stroke-width="1.2" fill="none"/></svg>
    <span>info@thebrightarchclinic.com</span>
  </div>

  <div class="abs bottom-bar"></div>
  <p class="abs copy">© <a>The Bright Arch Clinic</a> – 2019. All Rights Reserved.</p>
  <a class="abs credit">Harbor Falls Skin and Facial Care</a>
</footer>
</body>
</html>
```